Visitenkarten und Briefpapier
Zielgruppe
Planung und Realisierung von individuellen und wertbeständigen Kamin- und Ofenlösungen, sowie Fliesen- und Baddesign.
Aufgabenstellung
Wir benötigen ein möglichst schlichtes Design für Visitenkarten, bzw. Briefpapier. Für die Visitenkarten gerne auch Vorschläge mit Prägung, Ausstanzung oder mit Heißfolie. Auch Klappkarten wären denkbar. Das Design soll "das gewisse Etwas haben" und nicht zu verspielt sein.
Die Visitenkarten sind für die Firma KORVA, das Logo von der Ausstellung "raumfunke" soll dezent mit eingebunden werden (bei dem Briefpapier z.B. in der Fußzeile". Die farbliche Gestaltung sollte sich an den Farben des Logos orientieren.
Schriftart für Texte: Century Gothic
Schriftfarbe: RAL 7016
Nur eine Idee: Ich könnte mir auch gut vorstellen, dass die Visitenkarte aus einer Zündholzverpackung (wenn dann aber eine besondere mit nur einem Zündholz oder einem besonders breiten) besteht: http://glimmvelo.de/produkte_briefchen.php

```html
<!DOCTYPE html>
<html lang="de">
<head>
<meta charset="utf-8">
<title>KORVA – Briefpapier und Visitenkarte</title>
<link href="https://fonts.googleapis.com/css2?family=Questrial&display=swap" rel="stylesheet">
<style>
  :root{
    --board:#c89e6a;
    --paper:#ffffff;
    --anthracite:#25353a;
    --text:#2f3a3e;
    --flame:#f08a00;
    --shadow:rgba(60,40,15,.45);
  }
  html,body{margin:0;padding:0;overflow:hidden;}
  body{width:1200px;height:1120px;background:var(--board);position:relative;
       font-family:"Questrial","Century Gothic",sans-serif;color:var(--text);}
  .sheet,.card{position:absolute;box-shadow:6px 8px 10px var(--shadow);overflow:hidden;}
  .abs{position:absolute;margin:0;}

  /* Letterhead */
  .letterhead{left:58px;top:44px;width:730px;height:1032px;background:var(--paper);}
  .brand{font-size:50px;line-height:1;letter-spacing:2px;color:#111;}
  .letterhead .brand{right:42px;top:27px;}
  .letterhead .tagline{right:42px;top:81px;font-size:15.5px;color:var(--text);}
  .sender{left:547px;top:130px;font-size:14px;line-height:16.8px;font-style:normal;}
  .sender .spaced{letter-spacing:1.6px;}
  .sender .gap{margin-top:3px;}
  .partner{font-size:11px;color:#222;letter-spacing:.2px;line-height:1;}
  .letterhead .partner{right:35px;top:242px;}
  .return-line{left:92px;top:185px;font-size:8px;letter-spacing:1px;color:#222;display:flex;align-items:center;gap:5px;}
  .return-line .dot{width:4px;height:4px;background:var(--flame);}
  .fold-mark{width:4px;height:4px;background:var(--flame);}
  .punch-mark{left:0;width:0;height:0;border-top:6px solid transparent;border-bottom:6px solid transparent;border-left:6px solid var(--flame);}
  .footer{left:0;bottom:0;width:730px;height:95px;background:var(--anthracite);color:#fff;font-size:8px;line-height:12.3px;}
  .footer .legal{left:70px;top:15px;}
  .footer .bank{right:35px;top:15px;text-align:right;}
  .footer .mark{left:22px;top:40px;width:12px;height:12px;background:var(--flame);}

  /* Business card front */
  .card{width:334px;height:216px;left:827px;}
  .card-front{top:304px;background:var(--paper);}
  .card-front .brand{left:11px;top:13px;font-size:38px;letter-spacing:1.5px;}
  .card-front .tagline{left:11px;top:48px;font-size:11.5px;}
  .holder{right:20px;top:84px;text-align:right;}
  .holder .name{font-size:18.5px;color:var(--text);line-height:1.1;}
  .holder .role{font-size:8.5px;color:var(--flame);}
  .contact-band{left:0;bottom:0;width:334px;height:84px;background:var(--anthracite);color:#fff;font-size:11px;line-height:13.6px;}
  .contact-band .lines{left:11px;top:10px;}
  .contact-band .lines .mail{margin-top:2px;}
  .contact-band .web{right:12px;bottom:9px;}

  /* Business card back */
  .card-back{top:559px;background:var(--anthracite);}
  .back-brand{left:0;right:0;top:88px;text-align:center;font-size:40px;letter-spacing:3px;color:var(--flame);}
  .card-back .partner{right:9px;bottom:12px;color:#fff;text-align:right;font-size:11.5px;line-height:1;}
  .card-back .partner small{display:block;font-size:3px;letter-spacing:.3px;margin-top:1px;}
</style>
</head>
<body>

<section class="sheet letterhead" aria-label="Briefpapier">
  <div class="abs brand">KORVA</div>
  <div class="abs tagline">kamine · öfen · fliesen</div>

  <address class="abs sender">
    <div class="spaced">Am Lindenhang 12</div>
    <div class="spaced">34519 Diemelfeld</div>
    <div>fon:&nbsp;&nbsp; 05632 / 41 73 90</div>
    <div>fax:&nbsp;&nbsp;&nbsp; 05632 / 41 73 98</div>
    <div class="gap">info@korva-ofenbau.de</div>
    <div>www.korva-ofenbau.de</div>
  </address>
  <div class="abs partner">raumfunke</div>

  <div class="abs return-line"><span class="dot"></span>KORVA GmbH&nbsp; | &nbsp;Am Lindenhang 12&nbsp; | &nbsp;34519 Diemelfeld</div>

  <span class="abs fold-mark" style="left:72px;top:334px"></span>
  <span class="abs fold-mark" style="left:365px;top:334px"></span>
  <span class="abs punch-mark" style="top:358px"></span>
  <span class="abs punch-mark" style="top:723px"></span>

  <footer class="abs footer">
    <span class="abs mark"></span>
    <div class="abs legal">
      KORVA GmbH<br>
      Vertretungsberechtigter Geschäftsführer: Henrik Maurer<br>
      Registergericht: Amtsgericht Diemelfeld<br>
      Handelsregisternummer: HRB 556<br>
      Zuständige Kammer:<br>
      Handwerkskammer Nordhessen, Werkstraße 4, 34100 Talheim
    </div>
    <div class="abs bank">
      Bankverbindung:<br>
      Kreissparkasse Talheim<br>
      Konto-Nr.: 123 456<br>
      Blz: 520 400 10<br>
      BIC: TALHDE51XXX<br>
      IBAN: DE00 5204 0010 0000 1234 56
    </div>
  </footer>
</section>

<section class="card card-front" aria-label="Visitenkarte Vorderseite">
  <div class="abs brand">KORVA</div>
  <div class="abs tagline">kamine · öfen · fliesen</div>
  <div class="abs holder">
    <div class="name">Henrik Maurer</div>
    <div class="role">Geschäftsführer</div>
  </div>
  <div class="abs contact-band">
    <div class="abs lines">
      <div>Am Lindenhang 12</div>
      <div>34519 Diemelfeld</div>
      <div>fon:&nbsp;&nbsp; 05632 / 41 73 90</div>
      <div>fax:&nbsp;&nbsp; 05632 / 41 73 98</div>
      <div class="mail">info@korva-ofenbau.de</div>
    </div>
    <div class="abs web">www.korva-ofenbau.de</div>
  </div>
</section>

<section class="card card-back" aria-label="Visitenkarte Rückseite">
  <div class="abs back-brand">KORVA</div>
  <div class="abs partner">raumfunke<small>bauen raum leben</small></div>
</section>

</body>
</html>
```